Upscale business cards needed for Board of Directors

We need professional business cards created for members of our family business Board of Directors. We would like these relatively simple and straightforward, but also with a unique element to set them apart. Probably stick with neutral and simple colors - white, grey etc. We need space for the traditional elements, including name, title, address, email/phone number. And we will be creating several from this template so it needs to be template that is easy to switch information in and out of.
Business
See description

```html
<!DOCTYPE html>
<html lang="en">
<head>
<meta charset="utf-8">
<title>Kestrel Holdings – Business Card</title>
<link rel="stylesheet" href="https://fonts.googleapis.com/css2?family=Source+Sans+3:wght@400;600;700&display=swap">
<style>
  :root {
    --backdrop: #151515;
    --card-white: #f3f3f3;
    --card-gold: #b9a57c;
    --ink: #1b1b1b;
    --ink-soft: #2a2a2a;
    --reverse: #ffffff;
  }
  * { margin: 0; padding: 0; box-sizing: border-box; }
  html, body { width: 1200px; height: 900px; overflow: hidden; }
  body {
    background: var(--backdrop);
    font-family: "Source Sans 3", "Myriad Pro", Arial, sans-serif;
    position: relative;
  }
  .card {
    position: absolute;
    top: 185px;
    width: 302px;
    height: 489px;
    border-radius: 12px;
  }
  .card-front { left: 299px; background: var(--card-white); color: var(--ink); }
  .card-back { left: 646px; background: var(--card-gold); color: var(--reverse); }

  .brand-name {
    position: absolute;
    left: 0; right: 0;
    text-align: center;
    font-weight: 700;
    text-transform: uppercase;
    line-height: 1;
  }
  .card-front .brand-name { top: 58px; color: var(--ink); }
  .card-back .brand-name { top: 395px; color: var(--reverse); }
  .brand-name .line-main { display: block; font-size: 44px; letter-spacing: 1px; }
  .brand-name .line-sub { display: block; font-size: 24px; letter-spacing: 7px; margin-top: 6px; }

  .holder {
    position: absolute;
    left: 0; right: 0;
    top: 280px;
    text-align: center;
  }
  .holder-name { font-size: 17px; font-weight: 600; letter-spacing: 0.2px; color: var(--ink); }
  .holder-title { font-size: 14px; color: var(--ink-soft); margin-top: -2px; }

  .contact {
    position: absolute;
    left: 0; right: 0;
    top: 346px;
    text-align: center;
    font-size: 13.5px;
    line-height: 17px;
    color: var(--ink-soft);
    list-style: none;
  }
  .address {
    position: absolute;
    left: 0; right: 0;
    top: 421px;
    text-align: center;
    font-size: 13.5px;
    line-height: 16px;
    color: var(--ink-soft);
    font-style: normal;
  }
</style>
</head>
<body>
  <section class="card card-front" aria-label="Business card front">
    <h1 class="brand-name">
      <span class="line-main">Kestrel</span>
      <span class="line-sub">Holdings</span>
    </h1>
    <div class="holder">
      <p class="holder-name">DANIEL HARTLEY</p>
      <p class="holder-title">Managing Director</p>
    </div>
    <ul class="contact">
      <li>044-555-0182</li>
      <li>office@kestrelhold.com</li>
      <li>www.kestrelhold.com</li>
    </ul>
    <address class="address">
      48 Harbour Row Suite |<br>
      Northland, AB | 204816
    </address>
  </section>

  <section class="card card-back" aria-label="Business card back">
    <p class="brand-name">
      <span class="line-main">Kestrel</span>
      <span class="line-sub">Holdings</span>
    </p>
  </section>
</body>
</html>
```